Design 4 pages for an event discovery website

This is a contest for the design of 4 pages for an events discovery website. The feature is part of the new sign-up process.

Please see the attached document for a full scope, mockups and the parent category icons.

Target Market(s)

18-35 Australian event goers

Industry/Entity Type

Events

Number of Pages Required

4 page

```html
<!DOCTYPE html>
<html lang="en">
<head>
<meta charset="utf-8">
<title>evenzo – Link your accounts</title>
<link href="https://fonts.googleapis.com/css2?family=Open+Sans:ital,wght@0,400;0,600;0,700;1,700&display=swap" rel="stylesheet">
<style>
  :root {
    --ink: #ffffff;
    --ink-soft: #e8e8e8;
    --night: #050505;
    --rule: #6a6a6a;
    --crimson: #7a0a2a;
    --wine: #3a0614;
    --search-text: #9a9a9a;
    --chirper-a: #5cbde6;
    --chirper-b: #2a86bd;
    --snap-a: #c9a07c;
    --snap-b: #9c7352;
    --stream-a: #3cb02c;
    --stream-b: #14820e;
    --box-a: #3aa0ee;
    --box-b: #1050b4;
    --brand-dot: #f2c20c;
  }
  * { box-sizing: border-box; margin: 0; padding: 0; }
  html, body { width: 1200px; height: 792px; overflow: hidden; background: var(--night); }
  body { font-family: "Open Sans", Arial, sans-serif; color: var(--ink); position: relative; }

  .site-header {
    position: absolute; left: 0; top: 0; width: 1200px; height: 98px;
    background: var(--night); border-bottom: 1px solid var(--rule);
  }
  .brand { position: absolute; left: 36px; top: 22px; display: flex; align-items: center; gap: 10px; }
  .brand-dot { width: 34px; height: 34px; border-radius: 50%; background: var(--brand-dot); }
  .brand-name { font-size: 44px; font-weight: 700; color: var(--ink); line-height: 1; letter-spacing: -1px; }
  .nav-find { position: absolute; left: 302px; top: 37px; font-size: 12px; font-weight: 600; }
  .search {
    position: absolute; left: 786px; top: 30px; width: 204px; height: 38px;
    background: #fff; border-radius: 3px; display: flex; align-items: center; padding: 0 10px;
    color: var(--search-text); font-size: 15px;
  }
  .search svg { position: absolute; right: 12px; top: 11px; }
  .account-nav { position: absolute; left: 1019px; top: 38px; font-size: 15px; font-weight: 400; }
  .account-nav .sep { margin: 0 10px; }

  .stage {
    position: absolute; left: 0; top: 99px; width: 1200px; height: 633px;
    background:
      radial-gradient(circle at 72% 40%, rgba(170,20,60,.55), transparent 45%),
      radial-gradient(circle at 45% 85%, rgba(150,15,55,.5), transparent 40%),
      radial-gradient(circle at 95% 75%, rgba(140,10,50,.45), transparent 35%),
      linear-gradient(120deg, var(--night) 5%, var(--wine) 45%, var(--crimson) 100%);
  }

  .intro { position: absolute; left: 98px; top: 78px; list-style: none; }
  .intro li { position: relative; padding-left: 51px; font-size: 23px; font-weight: 600; line-height: 43px; margin-bottom: 15px; width: 760px; }
  .intro li svg { position: absolute; left: 0; top: 11px; }

  .link-list { position: absolute; left: 89px; top: 308px; }
  .link-row { display: flex; align-items: center; height: 60px; margin-bottom: 19.5px; }
  .link-btn {
    width: 305px; height: 60px; border-radius: 4px; display: flex; align-items: center;
    font-size: 22px; font-weight: 400; color: var(--ink); border: 1px solid rgba(255,255,255,.25);
  }
  .link-btn .mark { width: 55px; height: 100%; border-right: 1px solid rgba(0,0,0,.25); display: flex; align-items: center; justify-content: center; }
  .link-btn .mark span { width: 20px; height: 20px; background: var(--ink); border-radius: 2px; }
  .link-btn .label { padding-left: 23px; }
  .btn-chirper { background: linear-gradient(var(--chirper-a), var(--chirper-b)); }
  .btn-snap { background: linear-gradient(var(--snap-a), var(--snap-b)); }
  .btn-stream { background: linear-gradient(var(--stream-a), var(--stream-b)); }
  .btn-box { background: linear-gradient(var(--box-a), var(--box-b)); }
  .status { font-size: 19px; font-weight: 700; font-style: italic; margin-left: 15px; }
  .status.offset { margin-left: 60px; }

  .site-footer {
    position: absolute; left: 0; top: 732px; width: 1200px; height: 60px;
    background: var(--night); border-top: 1px solid var(--rule);
    display: flex; align-items: center; justify-content: center; font-size: 15px; color: var(--ink-soft);
  }
</style>
</head>
<body>
  <header class="site-header">
    <div class="brand"><span class="brand-dot"></span><span class="brand-name">evenzo</span></div>
    <div class="nav-find">FIND EVENT</div>
    <div class="search">search
      <svg width="16" height="16" viewBox="0 0 16 16"><circle cx="6.5" cy="6.5" r="5" fill="none" stroke="#b5b5b5" stroke-width="2"/><line x1="10.2" y1="10.2" x2="15" y2="15" stroke="#b5b5b5" stroke-width="2.4"/></svg>
    </div>
    <nav class="account-nav">SIGN UP<span class="sep">|</span>LOGIN</nav>
  </header>

  <main class="stage" role="img" aria-label="Dark crimson bokeh backdrop with soft glowing circles and sparkles">
    <ul class="intro">
      <li><svg width="28" height="24" viewBox="0 0 28 24"><path d="M3 22 C3 10 10 6 20 6" fill="none" stroke="#fff" stroke-width="4" stroke-linecap="round"/><path d="M16 1 L25 6 L16 11 Z" fill="#fff"/></svg>This is tracked at the top</li>
      <li><svg width="28" height="24" viewBox="0 0 28 24"><path d="M3 22 C3 10 10 6 20 6" fill="none" stroke="#fff" stroke-width="4" stroke-linecap="round"/><path d="M16 1 L25 6 L16 11 Z" fill="#fff"/></svg>Link in all your other social media account and music player</li>
      <li><svg width="28" height="24" viewBox="0 0 28 24"><path d="M3 22 C3 10 10 6 20 6" fill="none" stroke="#fff" stroke-width="4" stroke-linecap="round"/><path d="M16 1 L25 6 L16 11 Z" fill="#fff"/></svg>By Linking your account , we can save you a lot of time by automatically determine your interests</li>
    </ul>

    <div class="link-list">
      <div class="link-row">
        <div class="link-btn btn-chirper"><div class="mark"><span></span></div><div class="label">chirper</div></div>
        <div class="status">successfully linked an account</div>
      </div>
      <div class="link-row">
        <div class="link-btn btn-snap"><div class="mark"><span></span></div><div class="label">snapgram</div></div>
      </div>
      <div class="link-row">
        <div class="link-btn btn-stream"><div class="mark"><span></span></div><div class="label">tunestream</div></div>
        <div class="status offset">inked an account</div>
      </div>
      <div class="link-row">
        <div class="link-btn btn-box"><div class="mark"><span></span></div><div class="label">tunebox</div></div>
      </div>
    </div>
  </main>

  <footer class="site-footer">© 2015 evenzo. All Rights Reserved.</footer>
</body>
</html>
```